Brivolt Technologies business card design

We need a business card designed with our new logo. it would be great if the card could communicate it is a technology based company.

Target Market(s)

system integrators

Industry/Entity Type

technology, IOT

Contact Information for Business Card

Name, designation, Address, telephone number, email address

Requirements
Must have
• logo and company name
Nice to have
• something to do with technology

```html
<!DOCTYPE html>
<html lang="en">
<head>
<meta charset="utf-8">
<title>Brivolt Technologies – Business Card</title>
<link href="https://fonts.googleapis.com/css2?family=Montserrat:wght@700&family=Arimo:wght@400;700&display=swap" rel="stylesheet">
<style>
  :root{
    --stage:#1c1c1f;
    --card-dark:#3b3b3d;
    --card-light:#ffffff;
    --accent:#f39019;
    --ink-light:#ffffff;
    --ink-dark:#3b3b3d;
  }
  html,body{margin:0;padding:0;overflow:hidden;}
  body{width:1200px;height:864px;background:var(--stage);position:relative;font-family:"Arimo",Arial,sans-serif;}
  .card{position:absolute;left:300px;width:600px;height:343px;border-radius:22px;overflow:hidden;}
  .card--front{top:70px;background:var(--card-dark);}
  .card--back{top:451px;background:var(--card-light);}
  .brand{position:absolute;display:flex;align-items:center;gap:12px;z-index:1;}
  .brand__mark{width:28px;height:28px;background:var(--accent);flex:none;}
  .brand__name{font-family:"Montserrat",Arial,sans-serif;font-weight:700;line-height:1.05;letter-spacing:1px;text-transform:uppercase;white-space:nowrap;}
  .card--front .brand{left:50%;top:50%;transform:translate(-50%,-50%);gap:14px;}
  .card--front .brand__name{color:var(--ink-light);font-size:34px;}
  .card--front .brand__mark{width:44px;height:44px;}
  .card--back .brand{right:96px;top:34px;}
  .card--back .brand__name{color:var(--ink-dark);font-size:20px;}
  .wave{position:absolute;inset:0;}
  .contact{position:absolute;left:72px;top:188px;color:var(--ink-light);font-size:13px;line-height:1;z-index:1;}
  .contact__name{color:var(--accent);font-weight:700;font-size:19px;text-transform:uppercase;margin:0 0 5px;}
  .contact__role{margin:0 0 11px;}
  .contact__address{margin:0 0 9px;line-height:17px;}
  .contact__list{list-style:none;margin:0;padding:0;}
  .contact__list li{display:flex;align-items:center;gap:8px;height:16px;}
  .contact__list svg{width:12px;height:12px;flex:none;}
</style>
</head>
<body>
  <section class="card card--front">
    <div class="brand">
      <span class="brand__mark"></span>
      <span class="brand__name">Brivolt<br>Technologies</span>
    </div>
  </section>

  <section class="card card--back">
    <svg class="wave" viewBox="0 0 600 343" preserveAspectRatio="none">
      <path d="M0,290 C0,175 100,152 280,150 C440,146 560,130 600,60 L600,343 L0,343 Z" fill="var(--card-dark)"/>
      <path d="M-6,278 C-6,163 100,140 280,138 C440,134 556,118 592,50" fill="none" stroke="var(--accent)" stroke-width="4"/>
    </svg>
    <div class="brand">
      <span class="brand__mark"></span>
      <span class="brand__name">Brivolt<br>Technologies</span>
    </div>
    <div class="contact">
      <p class="contact__name">Dana Whitfield</p>
      <p class="contact__role">Co-Founder</p>
      <p class="contact__address">Lumen Plaza 2200 Harbor<br>Northgate Ave Suite 310</p>
      <ul class="contact__list">
        <li><svg viewBox="0 0 12 12"><path d="M2.5 1 L4.5 1 L5 3.5 L3.8 4.4 Q5 7 7.6 8.2 L8.5 7 L11 7.5 L11 9.5 Q11 11 9.5 11 Q1 10 1 2.5 Q1 1 2.5 1 Z" fill="var(--accent)"/></svg>555-014-2739</li>
        <li><svg viewBox="0 0 12 12"><rect x="0.5" y="2.5" width="11" height="7.5" fill="var(--accent)"/><path d="M0.5 2.5 L6 7 L11.5 2.5" fill="none" stroke="var(--card-dark)" stroke-width="1"/></svg>info@brivolt.com</li>
        <li><svg viewBox="0 0 12 12"><circle cx="6" cy="6" r="5.5" fill="var(--accent)"/><path d="M0.5 6 H11.5 M6 0.5 V11.5 M6 0.5 Q2.5 6 6 11.5 M6 0.5 Q9.5 6 6 11.5" fill="none" stroke="var(--card-dark)" stroke-width="0.8"/></svg>www.brivolt.com</li>
      </ul>
    </div>
  </section>
</body>
</html>
```